Velk Partners Building Business Cards

We need a business card that reflects our business as "Solar Experts" in San Diego. Browse our website www.velkpartners.example our License needs to be displayed as "CSLB# 3867140" our phone number is (619) 555-0187

Save thousands on your electric bills and increase the value of your home while helping to protect the environment. Our solar installation experts will help you design the system that's right for you, using only the highest quality equipment that will look great and give you ideal performance. Our goal is to make you energy independent, and get your electric bill to 0.

Paul Osterby
(619) 555-0187
paul@velkpartners.example

Target Market(s)

Home owners in san diego looking for solar

Industry/Entity Type

Solar Energy

Contact Information for Business Card

Paul Osterby
(619) 555-0187
paul@velkpartners.example

Font styles to use
Other font styles liked:
• Use our logo font

Requirements
Must have
• License needs to be displayed as "CSLB# 3867140" our phone number is (619) 555-0187
Nice to have
• Real images of rooftop home solar in san diego
Should not have
• our business address

```html
<!DOCTYPE html>
<html lang="en">
<head>
<meta charset="utf-8">
<title>Velk Partners Building – Business Cards</title>
<link rel="stylesheet" href="https://fonts.googleapis.com/css2?family=Open+Sans:wght@400;600;700&display=swap">
<style>
  :root {
    --navy: #1f3f86;
    --navy-deep: #17346f;
    --sun: #f6ae1b;
    --paper: #ffffff;
    --backdrop: #e9e7e3;
    --ink-light: #ffffff;
  }
  * { box-sizing: border-box; margin: 0; padding: 0; }
  html, body {
    width: 1200px; height: 950px; overflow: hidden;
    background: var(--backdrop);
    font-family: "Open Sans", Arial, sans-serif;
  }
  .sheet {
    position: relative; width: 1200px; height: 950px;
    display: flex; flex-direction: column; align-items: center; justify-content: center; gap: 50px;
  }
  .card {
    position: relative; width: 700px; height: 400px; overflow: hidden;
    box-shadow: 0 6px 18px rgba(0,0,0,.18);
  }
  /* Front */
  .card-front { background: var(--paper); }
  .card-front .waves { position: absolute; inset: 0; width: 100%; height: 100%; }
  .brand-name {
    position: absolute; left: 38px; top: 168px; width: 230px;
    color: var(--navy); font-weight: 700; font-size: 30px; line-height: 1.12;
    letter-spacing: -0.5px;
  }
  .contact {
    position: absolute; right: 36px; top: 56px; text-align: right;
    color: var(--ink-light); font-size: 15px; line-height: 1.35;
  }
  .contact .person { color: var(--sun); font-size: 21px; font-weight: 600; }
  .contact .role { font-size: 15px; margin-bottom: 22px; }
  .contact .line { display: flex; align-items: center; justify-content: flex-end; gap: 10px; margin-bottom: 6px; }
  .contact .line .spacer { width: 16px; }
  .icon { width: 16px; height: 16px; flex: none; }
  /* Back */
  .card-back { background: var(--sun); }
  .card-back .site {
    position: absolute; left: 50px; top: 50%;
    transform: translate(-50%, -50%) rotate(90deg); transform-origin: center;
    color: var(--ink-light); font-size: 14px; letter-spacing: 3px; white-space: nowrap;
    margin-left: 22px;
  }
  .back-mark {
    position: absolute; left: 50%; top: 50%; transform: translate(-50%, -50%);
    display: flex; align-items: center; gap: 18px;
  }
  .back-mark .dot { width: 64px; height: 64px; border-radius: 50%; background: var(--ink-light); }
  .back-mark .name { color: var(--ink-light); font-weight: 700; font-size: 34px; letter-spacing: -0.5px; }
</style>
</head>
<body>
<main class="sheet">
  <section class="card card-front" aria-label="Business card front">
    <svg class="waves" viewBox="0 0 700 400" preserveAspectRatio="none" aria-hidden="true">
      <path d="M296 0 C210 120 300 250 214 400 L700 400 L700 0 Z" fill="var(--navy-deep)"/>
      <path d="M306 0 C222 120 312 250 226 400 L700 400 L700 0 Z" fill="var(--sun)"/>
      <path d="M330 0 C246 120 336 250 250 400 L700 400 L700 0 Z" fill="var(--navy)"/>
    </svg>
    <div class="brand-name">Velk Partners Building</div>
    <div class="contact">
      <div class="person">Paul Osterby</div>
      <div class="role">CEO/Founder</div>
      <div class="line"><span>CSLB# 3867140</span><span class="spacer"></span></div>
      <div class="line"><span>(619) 555-0187</span>
        <svg class="icon" viewBox="0 0 16 16" aria-hidden="true"><path d="M4 1.5 6 5 4.6 6.6c.9 2 2.6 3.7 4.8 4.8L11 10l3.5 2-1 2.5C7.5 14.5 1.5 8.5 1.5 2.5Z" fill="var(--sun)"/></svg>
      </div>
      <div class="line"><span>paul@velkpartners.example</span>
        <svg class="icon" viewBox="0 0 16 16" aria-hidden="true"><rect x="1" y="3" width="14" height="10" rx="1" fill="var(--sun)"/><path d="M1.5 3.8 8 9l6.5-5.2" fill="none" stroke="var(--navy)" stroke-width="1.3"/></svg>
      </div>
      <div class="line"><span>www.velkpartners.example</span>
        <svg class="icon" viewBox="0 0 16 16" aria-hidden="true"><circle cx="8" cy="8" r="7" fill="var(--sun)"/><path d="M1 8h14M8 1c-3 3.5-3 10.5 0 14M8 1c3 3.5 3 10.5 0 14" fill="none" stroke="var(--navy)" stroke-width="1"/></svg>
      </div>
    </div>
  </section>

  <section class="card card-back" aria-label="Business card back">
    <div class="site">www.velkpartners.example</div>
    <div class="back-mark">
      <span class="dot"></span>
      <span class="name">Velk Partners Building</span>
    </div>
  </section>
</main>
</body>
</html>
```